Professional looking Roller Blind Discount Card that portrays quality at a value for money price!

We need a double sided business card designed as a discount card. Size 90mm wide x 55mm high.We would like it to look professional and portray quality at a value for money price point.I have uploaded a word document with a basic layout with the information we want included on each side of the card. Please put your own thought into the layout.

Contact Information for Business Card

As per word document attached.

```html
<!DOCTYPE html>
<html lang="en">
<head>
<meta charset="utf-8">
<title>Roller Blinds Discount Card</title>
<link rel="stylesheet" href="https://fonts.googleapis.com/css2?family=Poppins:wght@400;500;600;700&family=Oswald:wght@500;700&family=Dancing+Script:wght@600&display=swap">
<style>
  :root {
    --blue: #2aa5e3;
    --blue-deep: #1677c0;
    --ink: #4a4a4a;
    --card: #fbfbfb;
    --stage: #2a2a2c;
    --photo-a: #6b7a5a;
    --photo-b: #b9c4b0;
  }
  * { margin: 0; padding: 0; box-sizing: border-box; }
  html, body { width: 1200px; height: 874px; overflow: hidden; background: var(--stage); }
  body { position: relative; font-family: "Poppins", sans-serif; }

  .card {
    position: absolute; left: 290px; width: 620px; height: 379px;
    background: var(--card); overflow: hidden;
    box-shadow: 0 6px 18px rgba(0,0,0,.45);
  }
  .card--front { top: 43px; }
  .card--back { top: 452px; }

  /* front */
  .front-title {
    position: absolute; left: 34px; top: 14px;
    font-weight: 700; font-size: 74px; line-height: 1; color: var(--blue); letter-spacing: -1px;
  }
  .front-subtitle {
    position: absolute; left: 36px; top: 96px;
    font-size: 32px; font-weight: 400; color: var(--ink); letter-spacing: .5px;
  }
  .front-photo {
    position: absolute; left: 30px; top: 146px; width: 402px; height: 204px;
    border-radius: 18px; overflow: hidden;
    background: linear-gradient(135deg, #6e5a52 0%, var(--photo-a) 35%, var(--photo-b) 70%, #e6e8e2 100%);
  }
  .call-bar {
    position: absolute; left: 30px; top: 302px; width: 402px; height: 48px;
    background: linear-gradient(180deg, var(--blue), var(--blue-deep));
    border-radius: 0 0 18px 18px;
    color: #fff; font-size: 24px; font-weight: 400; line-height: 48px; text-align: center;
  }
  .call-bar strong { font-weight: 700; }
  .fabric-bubble { position: absolute; left: 448px; top: 168px; width: 160px; height: 110px; }
  .fabric-bubble text { font-family: "Dancing Script", cursive; font-size: 19px; fill: #fff; }
  .company-name {
    position: absolute; right: 22px; top: 318px;
    font-family: "Poppins", sans-serif; font-weight: 600; font-size: 20px; color: var(--blue);
    display: flex; align-items: center; gap: 8px;
  }
  .company-name .mark { width: 14px; height: 14px; background: var(--blue); }

  /* back */
  .badge { position: absolute; width: 170px; height: 170px; }
  .badge--free { left: 145px; top: 30px; }
  .badge--best { left: 22px; top: 178px; }
  .badge--family { left: 214px; top: 198px; }
  .badge-word { font-family: "Oswald", sans-serif; font-weight: 700; font-size: 50px; fill: #fff; }
  .badge-small { font-family: "Oswald", sans-serif; font-weight: 500; font-size: 11px; fill: #fff; letter-spacing: .3px; }

  .offer { position: absolute; left: 392px; top: 118px; width: 216px; }
  .offer-amount { font-weight: 700; font-size: 50px; line-height: 1; color: var(--blue); letter-spacing: -1px; white-space: nowrap; }
  .offer-product { margin-top: 6px; font-size: 19px; line-height: 1.12; color: var(--ink); }
  .offer-types { margin-top: 12px; font-size: 14px; line-height: 1.3; color: var(--ink); text-align: right; }
  .offer-types .dot { color: var(--blue); }
  .offer-call { margin-top: 14px; text-align: right; font-size: 21px; line-height: 1.15; color: var(--ink); }
  .offer-call .phone { color: var(--blue); font-weight: 700; display: block; }
</style>
</head>
<body>

<section class="card card--front">
  <h1 class="front-title">ROLLER BLINDS</h1>
  <p class="front-subtitle">FREE in Home Meacure &amp; Quote</p>
  <div class="front-photo" role="img" aria-label="Photo of a room with roller blinds on windows overlooking a leafy garden"></div>
  <div class="call-bar">CALL <strong>0400 123 987</strong> TODAY!</div>
  <svg class="fabric-bubble" viewBox="0 0 160 110" aria-label="Huge Selection of Fabrics">
    <defs>
      <linearGradient id="bubbleFill" x1="0" y1="0" x2="0" y2="1">
        <stop offset="0" stop-color="#4cb9ee"/>
        <stop offset="1" stop-color="#1677c0"/>
      </linearGradient>
    </defs>
    <ellipse cx="80" cy="46" rx="78" ry="43" fill="url(#bubbleFill)"/>
    <path d="M120 78 L150 108 L100 86 Z" fill="#1677c0"/>
    <text x="80" y="40" text-anchor="middle">Huge Selection</text>
    <text x="80" y="62" text-anchor="middle">of Fabrics</text>
  </svg>
  <div class="company-name"><span class="mark"></span>K&amp;M INTERIORS</div>
</section>

<section class="card card--back">
  <svg class="badge badge--free" viewBox="-85 -85 170 170" aria-label="Free in home measure and quote">
    <defs>
      <radialGradient id="sealFill" cx="0.4" cy="0.35" r="0.75">
        <stop offset="0" stop-color="#7fd0f5"/>
        <stop offset="0.6" stop-color="#2aa5e3"/>
        <stop offset="1" stop-color="#1677c0"/>
      </radialGradient>
      <g id="seal">
        <rect x="-68" y="-68" width="136" height="136" fill="url(#sealFill)"/>
        <rect x="-68" y="-68" width="136" height="136" fill="url(#sealFill)" transform="rotate(22.5)"/>
        <rect x="-68" y="-68" width="136" height="136" fill="url(#sealFill)" transform="rotate(45)"/>
        <rect x="-68" y="-68" width="136" height="136" fill="url(#sealFill)" transform="rotate(67.5)"/>
        <circle r="72" fill="url(#sealFill)"/>
      </g>
    </defs>
    <use href="#seal"/>
    <text class="badge-word" y="16" text-anchor="middle">FREE</text>
    <text class="badge-small" y="34" text-anchor="middle">IN HOME MEASURE &amp; QUOTE</text>
  </svg>

  <svg class="badge badge--best" viewBox="-85 -85 170 170" aria-label="Best price guarantee">
    <use href="#seal"/>
    <text class="badge-word" y="16" text-anchor="middle">BEST</text>
    <text class="badge-small" y="34" text-anchor="middle">PRICE GUARANTEE</text>
  </svg>

  <svg class="badge badge--family" viewBox="-85 -85 170 170" aria-label="Family owned and operated">
    <use href="#seal"/>
    <text class="badge-word" y="16" text-anchor="middle" style="font-size:42px">FAMILY</text>
    <text class="badge-small" y="34" text-anchor="middle">OWNED &amp; OPERATED</text>
  </svg>

  <div class="offer">
    <div class="offer-amount">25% OFF</div>
    <div class="offer-product">QUALITY CUSTOM<br>MADE ROLLER BLINDS</div>
    <div class="offer-types">BLOCKOUT <span class="dot">•</span> SCREEN<br>LIGHTFILTERING</div>
    <div class="offer-call">CALL<span class="phone">0400 123 987</span>TODAY!</div>
  </div>
</section>

</body>
</html>
```